3D instagram advertisement explaining function of mask

I need an infographic commercial for my instagram ad. The company is an online health product store, and one of our products are reusable N95 masks. I am looking for someone to use 3D images to show how my "Quolt mask" functions and what benefits come out of it. All masks have cartoon graphics on them and are made up of silver ion technology. which helps kill all virus and bacteria and blocks 5G radiation.

Target Market(s)

everyone

Industry/Entity Type

Health And Wellness

Font styles to use
Serif

Requirements
Must have
• -graphic of the mask and showing how the mask filters out bacteria and viruses
-one slide must show how many have been bought
-Canadian company must be emphasized
-graphics showing how 5G radiation bounces away from head
-warning slide stating that "the second wave is coming" and we need to protect ourselves early
Nice to have
• professional look but still fun since the masks are all cartoon characters

```html
<!DOCTYPE html>
<html lang="en">
<head>
<meta charset="utf-8">
<title>Quolt mask — The second wave is coming</title>
<link rel="stylesheet" href="https://fonts.googleapis.com/css2?family=Saira+Condensed:wght@600&display=swap">
<style>
  :root {
    --bg-light: #575757;
    --bg-mid: #2c2c2c;
    --bg-dark: #121212;
    --ink: #ffffff;
  }
  * { margin: 0; padding: 0; box-sizing: border-box; }
  html, body {
    width: 1200px;
    height: 675px;
    overflow: hidden;
    background: var(--bg-dark);
  }
  .slide {
    position: relative;
    width: 1200px;
    height: 675px;
    overflow: hidden;
    background: radial-gradient(ellipse 95% 110% at 50% 0%, var(--bg-light) 0%, var(--bg-mid) 45%, var(--bg-dark) 100%);
    font-family: "Saira Condensed", "Arial Narrow", sans-serif;
    color: var(--ink);
  }
  .brand {
    position: absolute;
    top: 150px;
    left: 0;
    width: 100%;
    display: flex;
    justify-content: center;
    align-items: center;
    gap: 12px;
  }
  .brand-dot {
    width: 14px;
    height: 14px;
    border-radius: 50%;
    background: var(--ink);
  }
  .brand-name {
    font-size: 32px;
    font-weight: 600;
    letter-spacing: 8px;
    line-height: 1;
  }
  .warning {
    position: absolute;
    top: 265px;
    left: 0;
    width: 100%;
    text-align: center;
    font-size: 51px;
    font-weight: 600;
    line-height: 76px;
    letter-spacing: 2.2px;
    text-transform: uppercase;
  }
</style>
</head>
<body>
  <main class="slide">
    <div class="brand">
      <span class="brand-dot"></span>
      <span class="brand-name">QUOLT</span>
    </div>
    <h1 class="warning">
      "The second wave is coming"<br>
      We need to protect ourselves early
    </h1>
  </main>
</body>
</html>
```